Letterhead Design for Law Firm

**Edit: I have added the photo of a bottom that I like.

------
We are looking for a re-design of our new letterhead. The letterhead is for a law firm and will be used for digital and traditionally printed correspondence.

Here are some suggestions:

- Please use colours are #8ec900 and simple black.
- Please do not use any type of "waves" at the bottom of the page. This is not in style at all.
- Please stay modern yet conservative.
- Please use font Segoe UI Light or similar if you can
- Avoid clipart or illustrations.
- Utilize ample white space in the layout so the design looks clean and information is easy to read at a glance. Don't overcrowd the letterhead.
- Make sure the letterhead design is consistent with our brand identity (see corvelith.ca)
-Please, no black headers or footers.

I am attaching my current letterhead and signature for your convenience.

Remember, the letterhead is an extension of our professional identity. We are a successful firm and trial lawyers who correspond with insurers, judges, lawyers, courts, clients, etc. Make it new, modern, attractive, yet powerful and conservative.

It needs to be easily printable. I would like the bleed removed in print so the black bar the bottom crosses the page (but the text is not near the edges)
Updates

Low design quality

Target Market(s)

Clients, Government Offices, Judiciary, Lawyers, Insurance Companies, Colleagues.

Industry/Entity Type

Law

Other font styles liked:
• Segoe UI LIght, Calibri Light,

Colors
00AB8E
00BBA5
67D7C9
C6EFE9
E9F9F6

Requirements
Must have
• Everything that is on the letterhead now.
Nice to have
• Cutting Edge design, yet conservative.
Should not have
• law firm cliche design, images,

```html
<!DOCTYPE html>
<html lang="en">
<head>
<meta charset="utf-8">
<title>Meridan Personal Injury Lawyers – Letterhead</title>
<link rel="stylesheet" href="https://fonts.googleapis.com/css2?family=Open+Sans:wght@300;400;600&display=swap">
<style>
  :root {
    --brand-green: #8ec900;
    --ink: #111111;
    --text-grey: #3c3c3c;
    --paper: #ffffff;
    --backdrop: #e4e6e8;
  }
  * { margin: 0; padding: 0; box-sizing: border-box; }
  html, body {
    width: 1200px; height: 1200px; overflow: hidden;
    background: var(--backdrop);
    font-family: "Open Sans", "Segoe UI", sans-serif;
  }
  .letterhead {
    position: absolute; left: 170px; top: 42px;
    width: 861px; height: 1115px;
    background: var(--paper);
    box-shadow: 0 2px 10px rgba(0,0,0,.12);
    overflow: hidden;
  }
  .side-rule {
    position: absolute; left: 32px; top: 0;
    width: 21px; height: 100%;
    background: var(--brand-green);
  }
  .firm-name {
    position: absolute; right: 31px; top: 30px;
    text-align: right; color: var(--ink);
    font-weight: 400;
  }
  .firm-name__word {
    display: block; font-size: 64px; line-height: 1;
    letter-spacing: 2px;
  }
  .firm-name__tagline {
    display: block; margin-top: 10px;
    font-size: 15.5px; letter-spacing: 2.2px;
  }
  .contact {
    position: absolute; right: 31px; top: 746px;
    list-style: none; text-align: right;
    font-weight: 300; font-size: 15.5px; color: var(--text-grey);
    line-height: 24.5px;
  }
  .contact li { display: flex; justify-content: flex-end; align-items: center; gap: 6px; }
  .contact svg { width: 14px; height: 14px; flex: none; fill: var(--brand-green); }
  .contact .contact__address { align-items: flex-start; line-height: 20px; margin-top: 2px; }
  .contact .contact__address svg { margin-top: 3px; }
  .contact .contact__address span { display: block; padding-right: 20px; }
  .contact .contact__address span:first-child { padding-right: 0; }
  .contact .contact__clerk { margin-top: 6px; padding-right: 2px; }
  .label-green { color: var(--brand-green); font-weight: 600; margin-right: 4px; }

  .practice {
    position: absolute; right: 31px; top: 944px; text-align: right;
  }
  .practice__title {
    color: var(--brand-green); font-weight: 400; font-size: 16px;
    margin-bottom: 4px;
  }
  .practice__list {
    list-style: none; font-weight: 300; font-size: 15.5px;
    color: var(--text-grey); line-height: 23px;
  }
  .practice__list li::after {
    content: ""; display: inline-block; width: 8px; height: 8px;
    margin-left: 8px; background: var(--brand-green);
    transform: rotate(45deg); vertical-align: 2px;
  }
  .edge-bar {
    position: absolute; right: 0; width: 11px; background: var(--ink);
  }
  .edge-bar--contact { top: 750px; height: 156px; }
  .edge-bar--practice { top: 950px; height: 133px; }

  .sign-off {
    position: absolute; left: 77px; top: 858px;
    font-size: 12.5px; color: var(--text-grey); font-weight: 600;
    line-height: 17px;
  }
  .sign-off__signature {
    width: 228px; height: 46px; margin: 8px 0 10px;
    background: linear-gradient(90deg, #f2f2f2, #e2e2e2);
  }
</style>
</head>
<body>
  <main class="letterhead">
    <div class="side-rule"></div>

    <header class="firm-name">
      <span class="firm-name__word">MERIDAN</span>
      <span class="firm-name__tagline">PERSONAL INJURY LAWYERS</span>
    </header>

    <ul class="contact">
      <li>905-555-0142
        <svg viewBox="0 0 24 24"><path d="M6.6 10.8a15.1 15.1 0 0 0 6.6 6.6l2.2-2.2a1 1 0 0 1 1-.25 11.4 11.4 0 0 0 3.6.57 1 1 0 0 1 1 1V20a1 1 0 0 1-1 1A17 17 0 0 1 3 4a1 1 0 0 1 1-1h3.5a1 1 0 0 1 1 1c0 1.25.2 2.45.57 3.57a1 1 0 0 1-.25 1z"/></svg>
      </li>
      <li>905-555-0187
        <svg viewBox="0 0 24 24"><path d="M6 2h12v6H6zM4 9h16a2 2 0 0 1 2 2v6h-4v5H6v-5H2v-6a2 2 0 0 1 2-2zm4 7v4h8v-4z"/></svg>
      </li>
      <li>clara@corvelith.ca
        <svg viewBox="0 0 24 24"><path d="M2 5h20v14H2zm2 2v.5l8 5 8-5V7l-8 5z"/></svg>
      </li>
      <li>www.CORVELITH.ca
        <svg viewBox="0 0 24 24"><path d="M12 2a10 10 0 1 0 0 20 10 10 0 0 0 0-20zm6.9 9h-3a15 15 0 0 0-1.3-5.6A8 8 0 0 1 18.9 11zM12 4.1c.9 1.3 1.8 3.7 1.9 6.9h-3.8c.1-3.2 1-5.6 1.9-6.9zM9.4 5.4A15 15 0 0 0 8.1 11h-3a8 8 0 0 1 4.3-5.6zM5.1 13h3a15 15 0 0 0 1.3 5.6A8 8 0 0 1 5.1 13zm6.9 6.9c-.9-1.3-1.8-3.7-1.9-6.9h3.8c-.1 3.2-1 5.6-1.9 6.9zm2.6-1.3a15 15 0 0 0 1.3-5.6h3a8 8 0 0 1-4.3 5.6z"/></svg>
      </li>
      <li class="contact__address">
        <div>
          <span>48 Harbour Street E., Suite 1210</span>
          <span>Hamilton, ON&nbsp; L8P 0X2</span>
        </div>
        <svg viewBox="0 0 24 24"><path d="M12 2a7 7 0 0 0-7 7c0 5 7 13 7 13s7-8 7-13a7 7 0 0 0-7-7zm0 9.5A2.5 2.5 0 1 1 12 6.5a2.5 2.5 0 0 1 0 5z"/></svg>
      </li>
      <li class="contact__clerk"><span class="label-green">File Clerk:</span>Clara Whitfield</li>
    </ul>
    <div class="edge-bar edge-bar--contact"></div>

    <section class="practice">
      <h2 class="practice__title">PRACTICE RESTRICTED</h2>
      <ul class="practice__list">
        <li>Serious Personal Injury</li>
        <li>Wrongful Death Litigation</li>
        <li>Long-Term Disability Litigation</li>
        <li>Wrongful Dismissal Litigation</li>
        <li>Employee Terminations</li>
      </ul>
    </section>
    <div class="edge-bar edge-bar--practice"></div>

    <section class="sign-off">
      <p>Yours Very Truly,</p>
      <p>MERIDAN PERSONAL INJURY LAWYERS</p>
      <div class="sign-off__signature" role="img" aria-label="Handwritten signature of Owen T. Meridan"></div>
      <p>Owen T. Meridan</p>
      <p>Meridan Law Professional Corporation</p>
      <p>/cw</p>
      <p>Encl.</p>
    </section>
  </main>
</body>
</html>
```